Finiding oppertunites in Real Estate 6.15.20

size of ad 7” x 9.6”
1-I like the ad to stand out and attract people's attention.
2-you should be able to see the text of the ad clearly .. see the attachment anything in yellow is instructions.
3-the list of topics should not be the main part of the ad
4-if you decide you want a picture or vector of a person .. (you decide)
then it should be a white male about 25-30 years old wearing a solid white or blue shirt and not long hair.
5-leave 1 inch for footer
see attachment
Good luck

Target Market(s)

potential male students 25-35 years of age

Industry/Entity Type

Education

Requirements
Must have
• will stand out and people would want to see it.
should be able to read the words of ad
Nice to have
• how to make money in real estate on one line

```html
<!DOCTYPE html>
<html lang="en">
<head>
<meta charset="utf-8">
<title>Real Estate Career Course</title>
<link href="https://fonts.googleapis.com/css2?family=Montserrat:wght@400;500;600;700;800&family=Oswald:wght@700&display=swap" rel="stylesheet">
<style>
  :root {
    --orange: #ea8c05;
    --blue: #0a6cbd;
    --navy: #0e4a8a;
    --ink: #111111;
    --grey-text: #3b3b3b;
    --panel: #f3f3f3;
    --strip: #e2e2e2;
    --white: #ffffff;
    --shape-line: #b9bcc2;
  }
  * { margin: 0; padding: 0; box-sizing: border-box; }
  html, body { width: 926px; height: 1200px; overflow: hidden; background: #ffffff; }
  .flyer {
    position: relative; width: 926px; height: 1200px; overflow: hidden;
    font-family: 'Montserrat', Arial, sans-serif;
    background: linear-gradient(120deg, #ffffff 0%, #f6f6f6 40%, #e9e9e9 100%);
  }
  .top-band { position: absolute; left: 0; top: 0; width: 926px; height: 155px; background: var(--orange); }
  .title-main {
    position: absolute; left: 0; top: 36px; width: 926px; text-align: center;
    color: var(--white); font-weight: 800; font-size: 66px; letter-spacing: 1px; line-height: 1;
  }
  .title-bar {
    position: absolute; left: 73px; top: 118px; width: 779px; height: 76px; background: var(--blue);
    color: var(--white); font-weight: 800; font-size: 52px; letter-spacing: 9px;
    display: flex; align-items: center; justify-content: center; line-height: 1;
  }
  .headline { position: absolute; left: 72px; top: 214px; line-height: 1; }
  .headline .q1 { font-size: 50px; font-weight: 700; color: var(--ink); }
  .headline .q1 em { font-style: normal; color: var(--orange); }
  .headline .q2 { font-size: 62px; font-weight: 800; color: var(--blue); margin-top: 12px; letter-spacing: -0.5px; }
  .audience { position: absolute; left: 74px; top: 362px; font-size: 29px; font-weight: 500; color: var(--ink); line-height: 36px; }
  .audience em { font-style: normal; font-weight: 700; color: var(--orange); }
  .rule { position: absolute; left: 73px; top: 446px; width: 352px; height: 2px; background: var(--orange); }
  .tagline { position: absolute; left: 74px; top: 467px; font-size: 35px; line-height: 41px; color: var(--grey-text); font-weight: 500; }
  .tagline .blue { color: var(--blue); font-weight: 800; font-size: 38px; }
  .tagline .orange { color: var(--orange); font-weight: 800; font-size: 38px; }
  .photo {
    position: absolute; left: 480px; top: 310px; width: 446px; height: 568px;
    background: radial-gradient(ellipse at 55% 55%, #2a57a0 0%, #1e4a8f 45%, rgba(30,74,143,0) 72%);
  }
  .badge { position: absolute; left: 0; top: 0; width: 926px; height: 1200px; }
  .topics {
    position: absolute; left: 0; top: 878px; width: 926px; height: 151px; background: var(--panel);
  }
  .topic-col { position: absolute; top: 14px; list-style: none; }
  .topic-col li {
    display: flex; align-items: center; gap: 8px; height: 26.5px;
    font-size: 16.5px; font-weight: 500; color: var(--ink);
  }
  .topic-col svg { width: 13px; height: 13px; flex: none; }
  .col-a { left: 63px; } .col-b { left: 378px; } .col-c { left: 702px; }
  .divider { position: absolute; top: 20px; width: 1px; height: 113px; background: var(--orange); }
  .div-a { left: 325px; } .div-b { left: 650px; }
  .slogan-strip {
    position: absolute; left: 0; top: 1029px; width: 926px; height: 45px; background: var(--strip);
    display: flex; align-items: center; justify-content: center;
    color: var(--navy); font-size: 21px; font-weight: 500;
  }
  .footer {
    position: absolute; left: 0; top: 1074px; width: 926px; height: 126px; background: var(--white);
    display: flex; align-items: center; justify-content: center;
    color: var(--navy); font-size: 25px; font-weight: 600;
  }
</style>
</head>
<body>
<main class="flyer">
  <div class="top-band"></div>
  <div class="title-main">REAL ESTATE</div>
  <div class="title-bar">CAREER COURSE</div>

  <h1 class="headline">
    <div class="q1">How to <em>Make Money</em> In</div>
    <div class="q2">REAL ESTATE?</div>
  </h1>

  <p class="audience">For those who have started or<br>would like to go into <em>Real Estate</em></p>
  <div class="rule"></div>

  <p class="tagline">
    <span class="blue">AN INVESTMENT</span><br>
    In Knowledge<br>
    <span class="orange">OPENS UP</span> Untold<br>
    Opportunities
  </p>

  <div class="photo" role="img" aria-label="Smiling young man in a blue suit, white shirt and navy tie"></div>

  <svg class="badge" viewBox="0 0 926 1200" aria-label="Remote sessions, 12 session course, classes starting June 16">
    <polygon points="149,648 412,691 191,781" fill="none" stroke="var(--shape-line)" stroke-width="3"/>
    <polygon points="98,668 375,656 353,759 109,754" fill="var(--orange)"/>
    <polygon points="143,722 322,718 319,776 147,774" fill="var(--blue)"/>
    <text x="234" y="712" text-anchor="middle" transform="rotate(-3 234 700)" fill="#fff"
          font-family="Montserrat, Arial, sans-serif" font-weight="800" font-size="37">REMOTE</text>
    <text x="232" y="767" text-anchor="middle" fill="#fff"
          font-family="Oswald, Arial Narrow, sans-serif" font-weight="700" font-size="44">SESSIONS</text>
    <rect x="248" y="783" width="228" height="28" fill="var(--blue)"/>
    <text x="362" y="804" text-anchor="middle" fill="#fff" font-family="Montserrat, Arial, sans-serif" font-weight="700" font-size="19">12 Session Course</text>
    <rect x="96" y="810" width="222" height="26" fill="var(--orange)"/>
    <text x="207" y="829" text-anchor="middle" fill="#fff" font-family="Montserrat, Arial, sans-serif" font-weight="500" font-size="17.5">CLASSES STARTING</text>
    <rect x="195" y="833" width="142" height="28" fill="var(--blue)"/>
    <text x="266" y="854" text-anchor="middle" fill="#fff" font-family="Montserrat, Arial, sans-serif" font-weight="800" font-size="19">JUNE 16</text>
  </svg>

  <section class="topics">
    <ul class="topic-col col-a">
      <li><svg viewBox="0 0 14 14"><circle cx="7" cy="7" r="6" fill="none" stroke="#ea8c05" stroke-width="1.3"/><path d="M4.2 7.2l2 2 3.6-4" fill="none" stroke="#ea8c05" stroke-width="1.4"/></svg>Single-family</li>
      <li><svg viewBox="0 0 14 14"><circle cx="7" cy="7" r="6" fill="none" stroke="#ea8c05" stroke-width="1.3"/><path d="M4.2 7.2l2 2 3.6-4" fill="none" stroke="#ea8c05" stroke-width="1.4"/></svg>Multifamily</li>
      <li><svg viewBox="0 0 14 14"><circle cx="7" cy="7" r="6" fill="none" stroke="#ea8c05" stroke-width="1.3"/><path d="M4.2 7.2l2 2 3.6-4" fill="none" stroke="#ea8c05" stroke-width="1.4"/></svg>Management</li>
      <li><svg viewBox="0 0 14 14"><circle cx="7" cy="7" r="6" fill="none" stroke="#ea8c05" stroke-width="1.3"/><path d="M4.2 7.2l2 2 3.6-4" fill="none" stroke="#ea8c05" stroke-width="1.4"/></svg>Real Estate Concepts</li>
      <li><svg viewBox="0 0 14 14"><circle cx="7" cy="7" r="6" fill="none" stroke="#ea8c05" stroke-width="1.3"/><path d="M4.2 7.2l2 2 3.6-4" fill="none" stroke="#ea8c05" stroke-width="1.4"/></svg>Real Estate law</li>
    </ul>
    <div class="divider div-a"></div>
    <ul class="topic-col col-b">
      <li><svg viewBox="0 0 14 14"><circle cx="7" cy="7" r="6" fill="none" stroke="#ea8c05" stroke-width="1.3"/><path d="M4.2 7.2l2 2 3.6-4" fill="none" stroke="#ea8c05" stroke-width="1.4"/></svg>Investment properties</li>
      <li><svg viewBox="0 0 14 14"><circle cx="7" cy="7" r="6" fill="none" stroke="#ea8c05" stroke-width="1.3"/><path d="M4.2 7.2l2 2 3.6-4" fill="none" stroke="#ea8c05" stroke-width="1.4"/></svg>Foreclosures</li>
      <li><svg viewBox="0 0 14 14"><circle cx="7" cy="7" r="6" fill="none" stroke="#ea8c05" stroke-width="1.3"/><path d="M4.2 7.2l2 2 3.6-4" fill="none" stroke="#ea8c05" stroke-width="1.4"/></svg>Rehab</li>
      <li><svg viewBox="0 0 14 14"><circle cx="7" cy="7" r="6" fill="none" stroke="#ea8c05" stroke-width="1.3"/><path d="M4.2 7.2l2 2 3.6-4" fill="none" stroke="#ea8c05" stroke-width="1.4"/></svg>Foreclosures</li>
      <li><svg viewBox="0 0 14 14"><circle cx="7" cy="7" r="6" fill="none" stroke="#ea8c05" stroke-width="1.3"/><path d="M4.2 7.2l2 2 3.6-4" fill="none" stroke="#ea8c05" stroke-width="1.4"/></svg>Short sales</li>
    </ul>
    <div class="divider div-b"></div>
    <ul class="topic-col col-c">
      <li><svg viewBox="0 0 14 14"><circle cx="7" cy="7" r="6" fill="none" stroke="#ea8c05" stroke-width="1.3"/><path d="M4.2 7.2l2 2 3.6-4" fill="none" stroke="#ea8c05" stroke-width="1.4"/></svg>Development</li>
      <li><svg viewBox="0 0 14 14"><circle cx="7" cy="7" r="6" fill="none" stroke="#ea8c05" stroke-width="1.3"/><path d="M4.2 7.2l2 2 3.6-4" fill="none" stroke="#ea8c05" stroke-width="1.4"/></svg>Finical modeling</li>
      <li><svg viewBox="0 0 14 14"><circle cx="7" cy="7" r="6" fill="none" stroke="#ea8c05" stroke-width="1.3"/><path d="M4.2 7.2l2 2 3.6-4" fill="none" stroke="#ea8c05" stroke-width="1.4"/></svg>HUD properties</li>
      <li><svg viewBox="0 0 14 14"><circle cx="7" cy="7" r="6" fill="none" stroke="#ea8c05" stroke-width="1.3"/><path d="M4.2 7.2l2 2 3.6-4" fill="none" stroke="#ea8c05" stroke-width="1.4"/></svg>Due Diligence e</li>
    </ul>
  </section>

  <div class="slogan-strip">An Investment In Knowledge ...</div>
  <footer class="footer">1 INCH FOR FOOTER</footer>
</main>
</body>
</html>
```